wealth management firm, professional group, new model

we have a logo that works but we need a card, white background using our colors...clean look

our tag line if can be used in

The Bridge From Client to Owner

```html
<!DOCTYPE html>
<html lang="en">
<head>
<meta charset="utf-8">
<title>Vela Wealth Partners – Business Card</title>
<link rel="stylesheet" href="https://fonts.googleapis.com/css2?family=Montserrat:wght@400;500;700&display=swap">
<style>
  :root {
    --navy: #14284b;
    --card: #ffffff;
    --backdrop: #efece7;
    --edge: #dedad3;
  }
  * { margin: 0; padding: 0; box-sizing: border-box; }
  html, body {
    width: 1200px;
    height: 896px;
    overflow: hidden;
    background: var(--backdrop);
    font-family: "Montserrat", Arial, sans-serif;
    color: var(--navy);
  }
  .stage {
    width: 1200px;
    height: 896px;
    display: flex;
    align-items: center;
    justify-content: center;
    gap: 48px;
  }
  .card {
    width: 532px;
    height: 304px;
    background: var(--card);
    border: 1px solid var(--edge);
    display: flex;
    flex-direction: column;
    align-items: center;
    text-align: center;
  }
  /* Front: personal details */
  .card-front { padding-top: 42px; }
  .person-name {
    font-weight: 700;
    font-size: 32px;
    letter-spacing: 5px;
    margin-right: -5px;
    line-height: 1;
  }
  .person-title {
    font-weight: 400;
    font-size: 19px;
    letter-spacing: 0.5px;
    margin-top: 8px;
  }
  .firm-line {
    margin-top: 52px;
    font-weight: 500;
    font-size: 14px;
    letter-spacing: 2px;
    margin-right: -2px;
    text-transform: uppercase;
  }
  .contact {
    margin-top: 56px;
    font-weight: 500;
    font-size: 15.5px;
    line-height: 23px;
  }
  .contact .divider { margin: 0 10px; }
  /* Back: firm name */
  .card-back {
    justify-content: center;
    gap: 18px;
  }
  .firm-name {
    font-weight: 500;
    font-size: 52px;
    letter-spacing: 30px;
    margin-right: -30px;
    line-height: 1;
  }
  .firm-descriptor {
    font-weight: 500;
    font-size: 19px;
    letter-spacing: 5px;
    margin-right: -5px;
  }
</style>
</head>
<body>
  <main class="stage">
    <section class="card card-front">
      <h1 class="person-name">JORDAN ELLIS</h1>
      <p class="person-title">Senior Wealth Advisor</p>
      <p class="firm-line">Vela Wealth Partners</p>
      <p class="contact">
        jordan@velawealth.com<span class="divider">|</span>+1(555) 310-4827<br>
        velawealth.com
      </p>
    </section>
    <section class="card card-back">
      <h2 class="firm-name">VELA</h2>
      <p class="firm-descriptor">WEALTH PARTNERS</p>
    </section>
  </main>
</body>
</html>
```